Design a Website in Wordpress for an Australian Health Training Company in Health related courses

We require a WORDPRESS based Website (due to add on's we need to use for third party software) to replace our old site.
We offer national face to face delivery in medical reception, terminology and also administration.
The website will have around 6 pages and the ability to describe our main 6 courses (perhaps on the Courses page this may be tabs opening up to details for example?)
I have attached a previous sample of a Joomla site which was being developed (please do not feel you have to copy this - but I am just giving it as a sample - copying would be boring). But it gives an idea of look/feel and colours which may be suitable. Open to other ideas though.
I will provide some of the content, but would like the ability to finish the content myself.
Images and graphics are important. While a few medical photos re great - don't be tempted to us all pictures of doctors and nurses (although a couple would be good) - these are administrative courses so general corporate, eye catching visionary pictures of people in general are great. A medical type picture is also fine.
THE BOOKING system - will be via an ADD ON which will occur at the end of the project and is supplied by a third party software company (our student management system). This project will include up to 2 hours working with the Tech guys from the third party software to enable the ADD ON. If this ADD ON requires more time, we will pay hourly (although I do not expect it will).
Target Market(s)
Mostly a female market, many mature aged women target 25-45 yrs. Mixture of medical/health and corporate. Maybe a bit of mums returning to work and corporate inspiration.
Industry/Entity Type
It Company
Coding
Coded - Design and coding required
Number of Pages Required
5+ page
Requirements
Must have
- Wordpress
- Great graphics
- Interesting
- professional and clean
- Enquiry section (info Pak)
- Should have a University feel to it - Education
- Pages
- Home Page - About Us - Recruitment -Courses - Class Schedule - Traineeships Queensland Funding - Latest News Blog - Corporate Training- Contact us

```html
<!DOCTYPE html>
<html lang="en">
<head>
<meta charset="utf-8">
<title>Harbourline Institute of Training</title>
<link href="https://fonts.googleapis.com/css2?family=Cinzel:wght@400;700&family=Open+Sans:ital,wght@0,400;0,600;0,700;1,400&display=swap" rel="stylesheet">
<style>
:root{
  --orange:#f7941d;
  --orange-dark:#e07e0a;
  --navy:#0f2f5c;
  --blue:#1d5fae;
  --sky:#2a73c4;
  --ink:#2b2b2b;
  --muted:#6b6b6b;
  --light:#f1f1f1;
  --line:#dcdcdc;
  --dark:#1e1e1e;
  --black:#111;
  --white:#fff;
}
*{box-sizing:border-box;margin:0;padding:0}
html,body{width:1200px;height:5070px;overflow:hidden}
body{font-family:"Open Sans",Arial,sans-serif;color:var(--ink);background:var(--white);font-size:14px;line-height:1.5;position:relative}
.section{position:absolute;left:0;width:1200px}
.abs{position:absolute}
.serif{font-family:"Cinzel",Georgia,serif}
.btn{display:inline-block;background:var(--orange);color:var(--white);font-size:12px;font-weight:600;padding:6px 16px;border-radius:2px}
.title{font-family:"Cinzel",Georgia,serif;font-size:30px;letter-spacing:1px;text-align:center;color:var(--ink)}
.title em{font-style:normal;color:var(--blue)}
.crest{width:34px;height:34px;border-radius:50%;background:var(--navy);margin:0 auto 8px}
.photo{border-radius:2px}
/* header */
.brand{display:flex;align-items:center;gap:10px}
.brand-dot{width:38px;height:38px;border-radius:50%;background:var(--navy)}
.brand-name{font-family:"Cinzel",Georgia,serif;font-size:15px;font-weight:700;color:var(--navy);line-height:1.15;width:160px}
.social{display:flex;gap:8px}
.social span{width:22px;height:22px;border-radius:50%;background:var(--navy);display:block}
.login{background:var(--orange);color:#fff;font-size:12px;padding:4px 14px;border-radius:12px}
.search{width:140px;height:26px;border:1px solid var(--line);border-radius:13px;font-size:12px;color:#999;padding:4px 12px}
.lang{width:90px;height:26px;border:1px solid var(--line);border-radius:13px;font-size:12px;padding:4px 10px;color:var(--ink)}
.contact{display:flex;align-items:center;gap:10px;font-size:13px}
.contact b{color:var(--blue);display:block;font-size:14px}
.ci{width:30px;height:30px;border-radius:50%;background:var(--orange);display:flex;align-items:center;justify-content:center}
.nav{left:100px;width:1000px;height:28px;background:var(--blue);display:flex;font-size:12.5px}
.nav a{color:#fff;text-decoration:none;padding:5px 14px}
.nav a.active{background:var(--orange)}
/* hero */
.hero-img{width:1200px;height:513px;background:linear-gradient(120deg,#b25a3a 0%,#6d3b34 35%,#2a3550 60%,#0f1c33 100%)}
.hero-title{left:100px;top:210px;background:rgba(0,0,0,.55);color:#fff;font-family:"Cinzel",Georgia,serif;font-size:30px;padding:6px 16px}
.hero-text{left:100px;top:272px;width:360px;background:rgba(0,0,0,.45);color:var(--orange);font-size:15px;padding:10px 16px;line-height:1.45}
/* welcome */
.welcome h1{font-family:"Cinzel",Georgia,serif;font-size:30px;font-weight:400;letter-spacing:1px}
.welcome h1 em{font-style:normal;color:var(--blue)}
.welcome p{font-size:13.5px;color:var(--ink);margin-bottom:10px}
.side-item{display:flex;gap:14px;margin-bottom:26px}
.side-icon{width:50px;height:50px;flex:none;display:flex;align-items:center;justify-content:center}
.side-item h4{font-family:"Cinzel",Georgia,serif;color:var(--blue);font-size:17px;font-weight:700}
.side-item p{font-size:12.5px;color:var(--muted);margin:0}
/* services */
.services{background:var(--light)}
.cols4{left:100px;width:1000px;display:flex;justify-content:space-between}
.svc{width:225px;text-align:center}
.svc-icon{width:100px;height:100px;border-radius:50%;border:5px solid var(--orange);background:#fff;margin:0 auto 18px;display:flex;align-items:center;justify-content:center}
.svc h3{font-family:"Cinzel",Georgia,serif;font-size:15px;font-weight:700;margin-bottom:8px}
.svc p{font-size:12px;color:var(--muted);margin-bottom:14px}
/* courses */
.grid3{left:100px;width:1000px;display:grid;grid-template-columns:repeat(3,295px);justify-content:space-between;row-gap:40px}
.course{text-align:center}
.course .photo{height:190px;margin-bottom:14px}
.course h3{font-family:"Cinzel",Georgia,serif;font-size:15px;font-weight:700;line-height:1.35;height:42px;margin-bottom:10px}
/* why */
.why{background:#f4f4f4}
.why-title{font-family:"Cinzel",Georgia,serif;font-size:30px;color:var(--orange);text-align:center}
.reason{display:flex;gap:18px;align-items:flex-start;position:absolute;width:620px}
.r-icon{width:64px;height:64px;border-radius:50%;background:var(--blue);flex:none;display:flex;align-items:center;justify-content:center;border:4px solid #fff;box-shadow:0 0 0 1px var(--line)}
.reason h4{color:var(--blue);font-size:17px;font-weight:600}
.reason p{font-size:13px;color:var(--ink)}
/* blog */
.h2{font-family:"Cinzel",Georgia,serif;font-size:28px}
.tweet{display:flex;gap:12px;border-bottom:1px solid var(--line);padding:10px 0;font-size:12px}
.tweet .av{width:34px;height:34px;background:#dfe6ee;flex:none}
.tweet b{color:var(--blue)}
/* candidate */
.cand{background:linear-gradient(90deg,#161616,#2a2a2a 50%,#161616)}
.cand h3{font-family:"Cinzel",Georgia,serif;color:#fff;font-size:32px;font-weight:400}
.cand p{color:#ddd;font-size:13px}
.cand p b{color:#fff}
/* enrol */
.enrol{background:var(--orange)}
.enrol p{color:#fff;font-size:25px;font-weight:700;line-height:1.35}
/* testimonials */
.quote{background:#eeeeee;padding:20px 26px;font-size:13.5px;color:var(--muted);width:475px}
.person{display:flex;align-items:center;gap:16px;font-family:"Cinzel",Georgia,serif;font-size:15px}
.person .av{width:60px;height:60px;border-radius:50%;background:#c9a98c}
/* footer */
.news{background:var(--dark);color:#fff}
.footer{background:var(--black);color:#ddd;font-size:12.5px}
.footer h4{color:#fff;font-size:17px;font-weight:600;margin-bottom:12px}
.footer ul{list-style:none}
.footer li{margin-bottom:8px}
.footer li:before{content:"› ";color:var(--orange)}
.field{background:#fff;height:26px;margin-bottom:8px;color:#888;font-size:12px;padding:4px 8px}
.copy{background:#000;color:#bbb;font-size:12.5px;text-align:center}
</style>
</head>
<body>

<!-- header -->
<header class="section" style="top:0;height:125px">
  <div class="abs brand" style="left:100px;top:16px">
    <span class="brand-dot"></span>
    <span class="brand-name">Harbourline Institute of Training</span>
  </div>
  <div class="abs social" style="left:300px;top:16px"><span></span><span></span><span></span><span></span></div>
  <div class="abs login" style="left:680px;top:14px">Login/Register</div>
  <div class="abs search" style="left:820px;top:12px">Search</div>
  <div class="abs lang" style="left:990px;top:12px">English ▾</div>
  <div class="abs contact" style="left:700px;top:58px">
    <span class="ci"><svg width="16" height="16" viewBox="0 0 24 24"><path fill="#fff" d="M6.6 10.8c1.4 2.8 3.8 5.1 6.6 6.6l2.2-2.2c.3-.3.7-.4 1-.2 1.1.4 2.3.6 3.6.6.6 0 1 .4 1 1V20c0 .6-.4 1-1 1C10.6 21 3 13.4 3 4c0-.6.4-1 1-1h3.5c.6 0 1 .4 1 1 0 1.3.2 2.5.6 3.6.1.3 0 .7-.2 1z"/></svg></span>
    <div><b>Call Us:</b>+61 (02) 5550 1842</div>
  </div>
  <div class="abs contact" style="left:910px;top:58px">
    <span class="ci"><svg width="16" height="16" viewBox="0 0 24 24"><rect x="3" y="6" width="18" height="12" fill="#fff"/><path d="M3 6l9 7 9-7" stroke="#f7941d" stroke-width="2" fill="none"/></svg></span>
    <div><b>Mail Us:</b>info@harbourline.example</div>
  </div>
</header>
<nav class="section nav" style="top:125px">
  <a class="active">Home</a><a>About Us</a><a>Recruitment</a><a>Courses</a><a>Class Schedule</a><a>Traineeships Queensland Funding</a><a>Latest News Blog</a><a>Corporate Training</a><a>Contact Us</a>
</nav>

<!-- hero -->
<section class="section" style="top:153px;height:513px">
  <div class="hero-img" role="img" aria-label="Photo of a businessman in a blue suit addressing a seated audience"></div>
  <div class="abs hero-title">Courses for Busy People</div>
  <div class="abs hero-text">Our unique quickFASTrack (Combined Assessment &amp; Training) class format delivers accelerated training that's specifically targeted at busy profes-sionals...</div>
</section>

<!-- welcome -->
<section class="section welcome" style="top:666px;height:450px">
  <div class="abs" style="left:100px;top:44px;width:26px;height:26px;border-radius:50%;background:var(--navy)"></div>
  <h1 class="abs" style="left:100px;top:86px">Welcome to <em>Harbourline Institute of Training</em></h1>
  <div class="abs" style="left:100px;top:150px;width:720px">
    <p>Harbourline is Australia's Leading Provider of Educational, Training and Support Services for the Medical and Dental industry - enabling students to be immediately skilled and 'Job Ready' for a career in Health.</p>
    <p>Harbourline is a Registered Training Organisation offering specialised Medical Administration Training in over 15 locations Australia wide. Harbourline have trained thousands of students the required knowledge and skills to become successful health care administrators.</p>
    <p>Our unique Short Medical Reception and Terminology Course and our Full Qualification is Nationally Accredited and the gold recognised qualification in industry.</p>
    <span class="btn" style="margin-top:6px">Read More</span>
  </div>
  <div class="abs" style="left:845px;top:130px;width:260px">
    <div class="side-item"><div class="side-icon"><svg width="44" height="44" viewBox="0 0 44 44"><path d="M8 6h22l6 6v26H8z" fill="none" stroke="#333" stroke-width="3"/><path d="M14 18h16M14 24h16M14 30h10" stroke="#333" stroke-width="2.5"/></svg></div><div><h4>Story</h4><p>Harbourline Health Management started business in February 1999 primarily... [ + ]</p></div></div>
    <div class="side-item"><div class="side-icon"><svg width="46" height="30" viewBox="0 0 46 30"><path d="M2 15C10 3 36 3 44 15 36 27 10 27 2 15z" fill="none" stroke="#333" stroke-width="3"/><circle cx="23" cy="15" r="7" fill="#333"/></svg></div><div><h4>Vision</h4><p>Harbourline Health Management started business in February 1999 primarily... [ + ]</p></div></div>
    <div class="side-item"><div class="side-icon"><svg width="46" height="30" viewBox="0 0 46 30"><path d="M3 14l10-8 10 6 10-6 10 8-12 12-8-6-8 6z" fill="none" stroke="#333" stroke-width="3" stroke-linejoin="round"/></svg></div><div><h4>Core Values</h4><p>Harbourline Health Management started business in February 1999 primarily... [ + ]</p></div></div>
  </div>
</section>

<!-- services -->
<section class="section services" style="top:1116px;height:540px">
  <div class="abs" style="left:0;top:40px;width:1200px">
    <div class="crest"></div>
    <h2 class="title">Our <em>Service</em></h2>
  </div>
  <div class="abs cols4" style="top:170px">
    <div class="svc"><div class="svc-icon"><svg width="50" height="50" viewBox="0 0 50 50"><rect x="6" y="8" width="38" height="26" fill="none" stroke="#333" stroke-width="3"/><circle cx="15" cy="40" r="5" fill="#333"/><path d="M18 22l8-6" stroke="#333" stroke-width="3"/></svg></div><h3>Training &amp; Assessment</h3><p>Lorem ipsum dolor sit amet, ectetuer adipiscing elit, sed diam nonummy nibh euismod tincidunt ut laoreet dolore</p><span class="btn">Read More</span></div>
    <div class="svc"><div class="svc-icon"><svg width="50" height="50" viewBox="0 0 50 50"><rect x="8" y="16" width="34" height="24" fill="none" stroke="#333" stroke-width="3"/><path d="M18 16v-6h14v6M8 26h34" stroke="#333" stroke-width="3" fill="none"/></svg></div><h3>Business &amp; Management</h3><p>Lorem ipsum dolor sit amet, ectetuer adipiscing elit, sed diam nonummy nibh euismod tincidunt ut laoreet dolore</p><span class="btn">Read More</span></div>
    <div class="svc"><div class="svc-icon"><svg width="50" height="50" viewBox="0 0 50 50"><path d="M10 24a15 15 0 0 1 30 0z" fill="#f7941d"/><rect x="8" y="24" width="34" height="4" fill="#333"/><path d="M14 32h22l-4 12H18z" fill="#333"/></svg></div><h3>Work Health &amp; Safety</h3><p>Lorem ipsum dolor sit amet, ectetuer adipiscing elit, sed diam nonummy nibh euismod tincidunt ut laoreet dolore</p><span class="btn">Read More</span></div>
    <div class="svc"><div class="svc-icon"><svg width="50" height="50" viewBox="0 0 50 50"><rect x="11" y="8" width="28" height="36" fill="none" stroke="#333" stroke-width="3"/><path d="M17 20l4 4 8-8M17 32h16" stroke="#333" stroke-width="3" fill="none"/></svg></div><h3>Project Management</h3><p>Lorem ipsum dolor sit amet, ectetuer adipiscing elit, sed diam nonummy nibh euismod tincidunt ut laoreet dolore</p><span class="btn">Read More</span></div>
  </div>
</section>

<!-- courses -->
<section class="section" style="top:1673px;height:900px">
  <div class="abs" style="left:0;top:30px;width:1200px">
    <div class="crest"></div>
    <h2 class="title">Our <em>Courses</em></h2>
  </div>
  <div class="abs grid3" style="top:140px">
    <div class="course"><div class="photo" style="background:linear-gradient(135deg,#c9b7a3,#8c7b6a)" role="img" aria-label="Photo of a receptionist assisting a patient at a medical front desk"></div><h3>Medical Reception<br>&amp; Terminology</h3><span class="btn">Read More</span></div>
    <div class="course"><div class="photo" style="background:linear-gradient(135deg,#e8eef4,#9aa6b8)" role="img" aria-label="Photo of a smiling business team in office attire"></div><h3>Cert III Business<br>Administration</h3><span class="btn">Read More</span></div>
    <div class="course"><div class="photo" style="background:linear-gradient(135deg,#e9edf2,#8aa0b8)" role="img" aria-label="Photo of a stethoscope and medical papers on a desk"></div><h3>Medical<br>Terminology</h3><span class="btn">Read More</span></div>
    <div class="course"><div class="photo" style="background:linear-gradient(135deg,#dfe7f0,#6f86a3)" role="img" aria-label="Photo of hands typing on a keyboard"></div><h3>Keyboard<br>and Typing</h3><span class="btn">Read More</span></div>
    <div class="course"><div class="photo" style="background:linear-gradient(135deg,#f4f6fa,#b9c8dd)" role="img" aria-label="Graphic of the word online with a computer mouse"></div><h3>Harbourline<br>Online</h3><span class="btn">Read More</span></div>
    <div class="course"><div class="photo" style="background:linear-gradient(135deg,#d7c3a4,#a5603f)" role="img" aria-label="Photo of a folder stamped confidential"></div><h3>Confidentiality<br>&nbsp;</h3><span class="btn">Read More</span></div>
  </div>
</section>

<!-- why choose us -->
<section class="section why" style="top:2585px;height:720px">
  <h2 class="abs why-title" style="left:0;top:22px;width:1200px">Why Choose Us</h2>
  <div class="abs" style="left:110px;top:200px;width:250px;text-align:center">
    <div class="serif" style="font-size:22px;font-weight:700;color:var(--navy);line-height:1.15;margin-bottom:18px">Harbourline Institute of Training</div>
    <div style="width:150px;height:150px;border-radius:50%;background:#dfe4ea;margin:0 auto"></div>
  </div>
  <svg class="abs" style="left:300px;top:90px" width="200" height="600" viewBox="0 0 200 600"><path d="M40 10 Q210 300 40 590" fill="none" stroke="#bfbfbf" stroke-width="4"/></svg>
  <div class="reason" style="left:410px;top:115px"><div class="r-icon"><svg width="28" height="28" viewBox="0 0 28 28"><circle cx="14" cy="11" r="8" fill="none" stroke="#fff" stroke-width="3"/><path d="M9 18l-2 9 7-4 7 4-2-9" fill="#fff"/></svg></div><div><h4>Quality</h4><p>Harbourline delivery quality, effective training facilitated by industry leaders. Just ask our students who rate us on average of 4.7 out of 5.</p></div></div>
  <div class="reason" style="left:465px;top:235px"><div class="r-icon"><svg width="28" height="28" viewBox="0 0 28 28"><circle cx="14" cy="14" r="11" fill="none" stroke="#fff" stroke-width="3"/><path d="M14 7v7l5 3" stroke="#fff" stroke-width="3" fill="none"/></svg></div><div><h4>Experience</h4><p>Harbourline is Australia's largest and leading providers of nationally recognised training in health administration - training from over 17 locations Australia wide.</p></div></div>
  <div class="reason" style="left:480px;top:355px"><div class="r-icon"><svg width="28" height="28" viewBox="0 0 28 28"><rect x="4" y="16" width="5" height="8" fill="#fff"/><rect x="12" y="10" width="5" height="14" fill="#fff"/><rect x="20" y="4" width="5" height="20" fill="#fff"/></svg></div><div><h4>Value</h4><p>Our innovative teaching approach allows us to deliver exceptional training at affordable prices with no hidden extras.</p></div></div>
  <div class="reason" style="left:465px;top:475px"><div class="r-icon"><svg width="28" height="28" viewBox="0 0 28 28"><circle cx="9" cy="10" r="5" fill="none" stroke="#fff" stroke-width="3"/><circle cx="19" cy="18" r="5" fill="none" stroke="#fff" stroke-width="3"/></svg></div><div><h4>Industry Recognised</h4><p>Harbourline work hand in hand with industry to develop our core programme and consolidate the programme annually to keep the programme fresh and relevant.</p></div></div>
  <div class="reason" style="left:410px;top:595px"><div class="r-icon"><svg width="28" height="28" viewBox="0 0 28 28"><rect x="6" y="4" width="16" height="20" fill="none" stroke="#fff" stroke-width="3"/><path d="M10 14l3 3 5-6" stroke="#fff" stroke-width="3" fill="none"/></svg></div><div><h4>Great Job Results</h4><p>Harbourline students get jobs! Our focus is to create job-ready students who are mentored to achieve their goals. Harbourline also provide a recruitment service for industry and graduates.</p></div></div>
</section>

<!-- blog & tweets -->
<section class="section" style="top:3400px;height:400px">
  <h2 class="abs h2" style="left:100px;top:30px">Latest Blog</h2>
  <div class="abs" style="left:540px;top:36px;font-size:16px;color:#555">‹ ›</div>
  <div class="abs" style="left:100px;top:85px;width:470px;height:210px;border:1px solid var(--line)">
    <div class="abs" style="left:10px;top:10px;width:200px;height:190px;background:linear-gradient(135deg,#e6ecf2,#8ea2b8)" role="img" aria-label="Photo of a smiling businessman in a shirt and tie"></div>
    <div class="abs" style="left:372px;top:-12px;width:66px;height:60px;background:var(--orange);color:#fff;text-align:center;font-weight:700;line-height:1.1;padding-top:8px"><span style="font-size:22px">26</span><br><span style="font-size:13px">June</span></div>
    <div class="abs" style="left:228px;top:60px;width:225px">
      <b style="font-size:15px">Lorem ipsum do sit amet.</b>
      <p style="font-size:12px;color:var(--muted);margin:6px 0 10px">Lorem ipsum dolor sit amet, consectetur adipiscing elit, sed do eiusmod tempor incididunt ut labore et dolore magna aliqua. Ut enim ad minim veniam.</p>
      <span class="btn">Read More</span>
    </div>
  </div>
  <h2 class="abs h2" style="left:635px;top:30px">Latest Tweets</h2>
  <div class="abs" style="left:1030px;top:36px;background:#e8eef4;border-radius:3px;font-size:12px;padding:2px 10px;color:var(--blue)">Follow</div>
  <div class="abs" style="left:635px;top:85px;width:470px">
    <div class="tweet"><div class="av"></div><div style="flex:1"><b>Ralph</b> @ralph<br>Lorem ipsum dolor sit amet, consectetur adipiscing elit, sed do eiusmod tempor incididunt ut labore et dolore mu</div><span style="color:#999">20 min</span></div>
    <div class="tweet"><div class="av"></div><div style="flex:1"><b>Ralph</b> @ralph<br>Lorem ipsum dolor sit amet, consectetur adipiscing elit, sed do eiusmod tempor incididunt ut labore et dolore mu</div><span style="color:#999">20 min</span></div>
    <div class="tweet"><div class="av"></div><div style="flex:1"><b>Ralph</b> @ralph<br>Lorem ipsum dolor sit amet, consectetur adipiscing elit, sed do eiusmod tempor incididunt ut labore et dolore mu</div><span style="color:#999">20 min</span></div>
  </div>
</section>

<!-- candidate / employer -->
<section class="section cand" style="top:3820px;height:290px" role="img" aria-label="Dark background photo of an office">
  <h3 class="abs" style="left:100px;top:20px">For the Candidate</h3>
  <div class="abs" style="left:100px;top:80px;width:370px">
    <p><b>Looking for a Career in Medical Administration?</b><br>Our partner company, Harbourline Institute of Training has been the market leader in Medical Reception Training in Australia for over 17 years. In fact, we pioneered it.</p>
    <span class="btn" style="margin-top:14px">Read More</span>
  </div>
  <div class="abs" style="left:490px;top:40px;width:220px;height:220px;border-radius:50%;background:#f2f2f2;border:6px solid #555;display:flex;align-items:center;justify-content:center;text-align:center">
    <span class="serif" style="font-size:17px;font-weight:700;color:var(--navy);width:150px;line-height:1.2">Harbourline Institute of Training</span>
  </div>
  <h3 class="abs" style="left:730px;top:20px">For the Employer</h3>
  <div class="abs" style="left:730px;top:80px;width:370px">
    <p>Harbourline Recruitment is a leading National Health Specialist Recruitment Agency with expertise in Medical and Dental administration recruitment for both permanent and temporary staff.</p>
    <span class="btn" style="margin-top:14px">Read More</span>
  </div>
</section>

<!-- enrol -->
<section class="section enrol" style="top:4110px;height:170px">
  <p class="abs" style="left:100px;top:38px;width:830px">Enrol In Our BSB51915 Diploma Of Leadership And Management And Gain Vaaluable Skills To Launch Your Management Career.</p>
  <div class="abs" style="left:980px;top:62px;background:#fff;color:var(--ink);font-weight:700;font-size:14px;padding:8px 16px">Booking Now</div>
</section>

<!-- testimonials -->
<section class="section" style="top:4290px;height:380px">
  <div class="abs" style="left:0;top:20px;width:1200px"><div class="crest"></div><h2 class="title">Client <em>Testimonials</em></h2></div>
  <div class="abs" style="left:80px;top:185px;font-size:22px;color:#ccc">‹</div>
  <div class="abs" style="left:1108px;top:185px;font-size:22px;color:#ccc">›</div>
  <div class="abs quote" style="left:110px;top:130px">Siam nonummy nibh euismod tincidunt ut laoreet do magna aliquam erat volutpat. Ut wisi enim ad minim veniam, vilium dolore eu feugiat nulla facilisis at vero eros et accumsan et iusto odio dig.</div>
  <div class="abs quote" style="left:615px;top:130px">Siam nonummy nibh euismod tincidunt ut laoreet do magna aliquam erat volutpat. Ut wisi enim ad minim veniam, vilium dolore eu feugiat nulla facilisis at vero eros et accumsan et iusto odio dig.</div>
  <div class="abs person" style="left:130px;top:265px"><span class="av" role="img" aria-label="Portrait photo of Mary Ellison"></span>Mary Ellison</div>
  <div class="abs person" style="left:635px;top:265px"><span class="av" role="img" aria-label="Portrait photo of David Marsh" style="background:#8a7b70"></span>David Marsh</div>
</section>

<!-- newsletter -->
<section class="section news" style="top:4670px;height:62px">
  <div class="abs" style="left:130px;top:20px;font-size:13px">Stay updated with latest news from</div>
  <div class="abs" style="left:390px;top:16px;width:270px;height:28px;background:#fff;color:#888;font-size:12px;padding:5px 10px">Enter Your Email</div>
  <div class="abs" style="left:690px;top:16px;background:#fff;color:var(--ink);font-size:13px;font-weight:700;padding:4px 14px">Subscribe</div>
  <div class="abs social" style="left:880px;top:19px"><span style="background:#666"></span><span style="background:#666"></span><span style="background:#666"></span><span style="background:#666"></span><span style="background:#666"></span></div>
</section>

<!-- footer -->
<footer class="section footer" style="top:4732px;height:298px">
  <div class="abs" style="left:100px;top:22px;width:300px">
    <h4>Quick Link</h4>
    <div style="display:flex;gap:30px">
      <ul><li>Home</li><li>About Us</li><li>Courses</li><li>Recruitment</li><li>Class Schedule</li><li>Traineeships Queensland Funding</li></ul>
      <ul><li>Latest News Blog</li><li>Corporate Training</li><li>Contact Us</li></ul>
    </div>
  </div>
  <div class="abs" style="left:380px;top:22px;width:240px">
    <h4>Information</h4>
    <p style="margin-bottom:10px">⌖ Harbourline Health Trainings<br>&nbsp;&nbsp;&nbsp;12 Larkin Street, Level 3,<br>&nbsp;&nbsp;&nbsp;Springfield QLD 4300</p>
    <p style="margin-bottom:10px">✆ +61 (02) 5550 1842</p>
    <p>✉ info@harbourline.example</p>
  </div>
  <div class="abs" style="left:640px;top:22px;width:190px">
    <h4>Info Pak</h4>
    <div class="field">Name</div>
    <div class="field">Email</div>
    <div style="display:flex;gap:8px"><div class="field" style="flex:1">Course ▾</div><div class="field" style="flex:1">State ▾</div></div>
    <div class="field" style="height:48px">Message</div>
    <div style="background:#fff;color:var(--ink);display:inline-block;font-weight:700;font-size:12px;padding:3px 12px">Submit</div>
  </div>
  <div class="abs" style="left:960px;top:50px;width:150px;text-align:center">
    <div class="serif" style="font-size:15px;font-weight:700;color:#ddd;line-height:1.2;margin-bottom:12px">Harbourline Institute of Training</div>
    <div style="width:70px;height:70px;border-radius:50%;background:#444;margin:0 auto"></div>
  </div>
</footer>
<div class="section copy" style="top:5030px;height:40px;padding-top:11px">© 2016 Harbourline Health Trainings. All Right Reserved</div>

</body>
</html>
```